Need webdesign for service company that provides Car hiring service and transit service

We need a web design for a company that provides airport transit services and transport services including Limo, Corporate cars, Disability transit, Family transit service. We need is a simple and professional design.

Below is site which we like and also offer the same service http://www.ridelarkway.com.au/
Updates

Project Deadline Extended
Reason: Waiting for the Feedback from multiple stakeholders. Need the time to select and approve the design

Target Market(s)

Tourism, Travel

Industry/Entity Type

Airport

Number of Pages Required

3 page

Font styles to use
Decorative
Script

Requirements
Must have
• Simple and Professional, Site we like http://www.ridelarkway.com.au/ and also need to mobile friendly
Should not have
• Shouldn't have too many images

```html
<!DOCTYPE html>
<html lang="en">
<head>
<meta charset="utf-8">
<title>Ridely — Private &amp; Business Transport</title>
<link rel="stylesheet" href="https://fonts.googleapis.com/css2?family=Montserrat:wght@300;400;500&family=Open+Sans:wght@400;600;700;800&display=swap">
<style>
  :root{
    --ink:#111111;
    --muted:#666666;
    --page:#ebecee;
    --white:#ffffff;
    --panel:#686364;
    --tile-black:#000000;
    --tile-charcoal:#414042;
    --tile-slate:#58585a;
    --tile-taupe:#7a7475;
    --tile-stone:#858384;
    --accent:#ffcc00;
    --accent-text:#555555;
    --arrow:#b5b5b7;
  }
  *{margin:0;padding:0;box-sizing:border-box}
  html,body{width:1200px;height:1123px;overflow:hidden}
  body{position:relative;background:var(--page);font-family:"Montserrat",sans-serif;color:var(--ink)}

  .site-header{position:absolute;left:0;top:0;width:1200px;height:98px;background:var(--white)}
  .brand{position:absolute;left:132px;top:27px;display:flex;align-items:center;gap:12px}
  .brand-mark{width:34px;height:34px;border:3px solid var(--ink)}
  .brand-name{font-family:"Montserrat",sans-serif;font-weight:500;font-size:32px;letter-spacing:-0.5px;color:var(--ink)}
  .header-actions{position:absolute;top:22px;left:890px;display:flex;gap:10px}
  .header-actions svg{width:53px;height:53px;display:block}

  .intro{position:absolute;left:0;top:140px;width:1200px;text-align:center}
  .intro h1{font-weight:400;font-size:35px;line-height:46px}
  .intro h2{font-weight:400;font-size:17px;margin-top:12px;color:#333}
  .intro p{font-weight:300;font-size:15px;line-height:23px;color:var(--muted);margin-top:26px}

  .quote{position:absolute;left:142px;top:329px;width:385px;height:377px;background:var(--panel);font-family:"Open Sans",sans-serif;color:var(--white)}
  .quote h3{position:absolute;left:32px;top:26px;font-weight:600;font-size:23px}
  .field{position:absolute;left:32px;width:308px;height:46px;background:var(--white);display:flex;align-items:center;color:#333;font-size:11.5px}
  .field .ico{width:39px;height:26px;border-right:1px solid #ccc;display:flex;align-items:center;justify-content:center;margin-right:14px}
  .field.origin{top:81px}
  .field.destination{top:137px}
  .option{position:absolute;left:37px;display:flex;align-items:center;gap:10px;font-size:11px;font-weight:600;text-transform:uppercase}
  .option.stops{top:207px}
  .option.vehicles{top:238px}
  .estimate{position:absolute;left:32px;top:279px;width:308px;height:58px;background:var(--accent);color:var(--accent-text);font-weight:800;font-size:26px;display:flex;align-items:center;justify-content:center;letter-spacing:0.3px}

  .tile{position:absolute;display:flex;flex-direction:column;align-items:center;justify-content:center;font-family:"Open Sans",sans-serif;font-size:16px;color:var(--white);text-align:center;line-height:22px}
  .tile svg{display:block;margin-bottom:14px}
  .t-limo{left:560px;top:327px;width:154px;height:123px;background:var(--tile-black)}
  .t-corporate{left:720px;top:329px;width:166px;height:123px;background:var(--tile-charcoal)}
  .t-disability{left:893px;top:329px;width:166px;height:123px;background:var(--tile-slate)}
  .t-transport{left:560px;top:456px;width:154px;height:250px;background:#3f3e40}
  .t-airport{left:720px;top:457px;width:339px;height:123px;background:var(--tile-taupe);font-weight:600}
  .t-driver{left:720px;top:585px;width:166px;height:123px;background:var(--tile-stone);font-weight:600}
  .t-contact{left:893px;top:585px;width:166px;height:123px;background:var(--tile-black);font-weight:600}
  .driver-figure{width:46px;height:48px;background:linear-gradient(#f2f2f2,#cfcfcf);border-radius:18px 18px 4px 4px;margin-bottom:14px}

  .news{position:absolute;left:0;top:776px;width:1200px;text-align:center}
  .news h2{font-weight:400;font-size:35px;line-height:46px}
  .news p{font-weight:400;font-size:17px;line-height:28px;color:var(--muted);margin-top:40px}
  .news-arrow{position:absolute;top:868px}
  .news-arrow.prev{left:308px}
  .news-arrow.next{left:853px}
  .read-more{position:absolute;left:544px;top:942px;width:112px;height:37px;background:var(--tile-black);color:var(--white);font-weight:600;font-size:13px;display:flex;align-items:center;justify-content:center}

  .site-footer{position:absolute;left:0;top:1030px;width:1200px;height:93px;background:var(--white);font-size:11px;color:#222}
  .footer-brand{position:absolute;left:134px;top:37px;display:flex;align-items:center;gap:14px}
  .footer-brand .brand-mark{width:22px;height:22px;border-width:2px}
  .footer-links{position:absolute;right:129px;top:40px}
  .footer-links span{margin:0 5px;color:#444}
</style>
</head>
<body>
  <header class="site-header">
    <div class="brand"><span class="brand-mark"></span><span class="brand-name">RIDELY</span></div>
    <nav class="header-actions" aria-label="Quick actions">
      <svg viewBox="0 0 53 53" aria-label="Menu"><rect x="11" y="11" width="31" height="31" transform="rotate(45 26.5 26.5)" fill="none" stroke="#111" stroke-width="1.6"/><path d="M19 21h15M19 26.5h15M19 32h15" stroke="#111" stroke-width="2.6"/></svg>
      <svg viewBox="0 0 53 53" aria-label="Call"><rect x="11" y="11" width="31" height="31" transform="rotate(45 26.5 26.5)" fill="none" stroke="#111" stroke-width="1.6"/><path d="M21 20c-1 2 1 7 5 10s6 4 8 2l-3-3-2 1c-2-1-4-3-5-5l1-2z" fill="#111"/></svg>
      <svg viewBox="0 0 53 53" aria-label="Search"><rect x="11" y="11" width="31" height="31" transform="rotate(45 26.5 26.5)" fill="none" stroke="#111" stroke-width="1.6"/><circle cx="25" cy="25" r="5" fill="none" stroke="#111" stroke-width="2.4"/><path d="M29 29l4 4" stroke="#111" stroke-width="2.6"/></svg>
    </nav>
  </header>

  <section class="intro">
    <h1>Private &amp; Business</h1>
    <h2>Personalised Transport Service</h2>
    <p>It is a long established fact that a reader will be distracted by the<br>readable content of a page when looking.</p>
  </section>

  <form class="quote">
    <h3>Get Instant Quote</h3>
    <div class="field origin"><span class="ico"><svg width="12" height="12"><circle cx="6" cy="6" r="4.5" fill="none" stroke="#555" stroke-width="1.5"/></svg></span>Origin (Public Location or Exact Address</div>
    <div class="field destination"><span class="ico"><svg width="10" height="14"><path d="M5 13C2 9 1 7 1 5a4 4 0 0 1 8 0c0 2-1 4-4 8z" fill="#555"/><circle cx="5" cy="5" r="1.6" fill="#fff"/></svg></span>Destination (Public Location or Exact Address</div>
    <div class="option stops"><svg width="12" height="12"><path d="M6 0v12M0 6h12" stroke="#fff" stroke-width="2.6"/></svg>Add stops</div>
    <div class="option vehicles"><svg width="14" height="11"><path d="M2 5l2-4h6l2 4h1v5h-2V9H3v1H1V5z" fill="#fff"/></svg>Show other vehicles</div>
    <div class="estimate">ESTIMATE FARE</div>
  </form>

  <a class="tile t-limo"><svg width="90" height="20" viewBox="0 0 90 20"><path d="M2 12l8-5h16l4-3h36l6 3h14l2 4v4H2z" fill="#fff"/><circle cx="14" cy="15" r="4" fill="#000" stroke="#fff" stroke-width="1.5"/><circle cx="76" cy="15" r="4" fill="#000" stroke="#fff" stroke-width="1.5"/></svg>Limo</a>
  <a class="tile t-corporate"><svg width="70" height="28" viewBox="0 0 70 28"><path d="M2 20v-8l6-2 6-8h28l10 8 14 3v7z" fill="#fff"/><path d="M17 4h10v7H13zM31 4h9l7 7H31z" fill="#414042"/><circle cx="12" cy="21" r="5" fill="#414042" stroke="#fff" stroke-width="2"/><circle cx="56" cy="21" r="5" fill="#414042" stroke="#fff" stroke-width="2"/></svg>Corporate cars</a>
  <a class="tile t-disability"><svg width="46" height="38" viewBox="0 0 46 38"><rect x="6" y="8" width="34" height="22" fill="none" stroke="#fff" stroke-width="2.5"/><rect x="16" y="2" width="14" height="6" fill="none" stroke="#fff" stroke-width="2.5"/><g fill="#fff"><circle cx="3" cy="36" r="2"/><circle cx="11" cy="36" r="2"/><circle cx="19" cy="36" r="2"/><circle cx="27" cy="36" r="2"/><circle cx="35" cy="36" r="2"/><circle cx="43" cy="36" r="2"/></g></svg>Disability transit</a>
  <a class="tile t-transport"><svg width="84" height="32" viewBox="0 0 84 32"><rect x="8" y="2" width="50" height="22" fill="none" stroke="#fff" stroke-width="3"/><path d="M60 8h12l6 8v8H60z" fill="none" stroke="#fff" stroke-width="3"/><path d="M0 30h84" stroke="#fff" stroke-width="2.5"/><circle cx="20" cy="25" r="3.5" fill="#fff"/><circle cx="68" cy="25" r="3.5" fill="#fff"/></svg>Transport<br>Services</a>
  <a class="tile t-airport"><svg width="54" height="40" viewBox="0 0 54 40"><path d="M6 2l4 0 6 14 12 2 20 6c4 2 4 5 0 5L6 22z" fill="#fff"/><path d="M0 38h54" stroke="#fff" stroke-width="3"/></svg>Airport Transit</a>
  <a class="tile t-driver"><div class="driver-figure" role="img" aria-label="Chauffeur figure icon"></div>Become a Driver</a>
  <a class="tile t-contact"><svg width="40" height="30" viewBox="0 0 40 30"><rect x="2" y="2" width="36" height="26" fill="none" stroke="#fff" stroke-width="3"/><path d="M2 3l18 14L38 3" fill="none" stroke="#fff" stroke-width="3"/></svg>Contact</a>

  <section class="news">
    <h2>News &amp; Events</h2>
    <p>Lorem Ipsum is simply dummy text of the printing and<br>typese industry Lorem Ipsum has been</p>
  </section>
  <svg class="news-arrow prev" width="20" height="30" viewBox="0 0 20 30"><path d="M16 2L4 15l12 13" fill="none" stroke="var(--arrow)" stroke-width="4"/></svg>
  <svg class="news-arrow next" width="20" height="30" viewBox="0 0 20 30"><path d="M4 2l12 13L4 28" fill="none" stroke="var(--arrow)" stroke-width="4"/></svg>
  <a class="read-more">READ MORE</a>

  <footer class="site-footer">
    <div class="footer-brand"><span class="brand-mark"></span><span>Copyrihgts @ 2017 All Rights Reserved</span></div>
    <div class="footer-links">Home<span>|</span>Sitemap<span>|</span>Privacy policy<span>|</span>Terms &amp; Conditions</div>
  </footer>
</body>
</html>
```